Artificial Intelligence Software Product Microsite

We specialises in Artificial Intelligence (AI) technology for big data analytics and we have a new product to be launched and requires a product microsite for it. Our product is an AI-driven Predictive/Prescriptive Analytics Engine that does the job of a Data Scientist or a group of Data Scientists, highly intelligent and fully automated, where endusers do not require any machine-learning knowledge. We would like to see a design that's simple yet futuristic and provide an impression that it is highly technological advanced. Key messages to deliver are that it is first of its kind in the world, it deploys state-of-the-art technology, a solution that is easy to adopt and integrate into their existing or planned apps. It is in effect a (or a pool of) Virtual Data Scientist(s) at their disposal that will work for them tirelessly 365 days a year and at a small fraction of the cost of a data scientist. Will provide more details, files/images only to shortlisted designers. Expecting something that is simple and straightforward that sufficiently showcase the product/technology.

Deadline will be extended if necessary to facilitate shortlisted designers.
Updates

Reason: To provide designers with more time for submission and amendments. For those who have not submitted your design, pls do so ASAP and also submit your concept first. Pls ensure that you are designing a Product Micro-site and not a corporate website. It's meant to introduce the product only, not the company. Only an enquiry email address is to be included at the bottom. Already said in my earlier public comments, would want something that is scroll-down to view more info rather then having to click to view different pages. This is a pre-requisite as stated both in my project brief and public comments. Thank you for participating and looking forward to see something really good soon.

Target Market(s)

App Developers in the Software Industry or any Enterprise Customers with in-house apps.

Industry/Entity Type

Computer Software

Coding

Coded - Design and coding required

Number of Pages Required

3 page

Font styles to use
Other font styles liked:
• Pls refer to attachments.

Requirements
Must have
• Please refer to the attached document "BrambleAI 1-page Infosheet". Key message to be delivered is as per this document but need to add in additional information on performance comparisons, which is a small section but only ready on 10th Jul. The microsite doesn't have to be strictly 3 pages but can be less or more if necessary but do go along the lines of the modern sites whereby when options are clicked, the page slides down to the specific option selected instead. Prefers some simple animation, especially for the diagram that depicts the high-level architecture of our AI engine, how the process flows between the different components. Make it simple yet futuristic. The key theme or focal point is "Virtual Data Scientist". Would like to see something that's short and straight to the point, with a clean design.
Nice to have
• If you can use suitable images of a (or group of) human data scientist(s) depicting the transformation to a "Virtual Data Scientist" will be great.
Should not have
• This is a software technology to be introduced and as such, must have a design or theme appropriate for the industry. It should not have the kind of generic look-and-feel that other industries uses.

```html
<!DOCTYPE html>
<html lang="en">
<head>
<meta charset="utf-8">
<title>BrambleAI – Virtual Data Scientist</title>
<link href="https://fonts.googleapis.com/css2?family=Raleway:wght@300;400;500;600;700&family=Open+Sans:wght@400;600&display=swap" rel="stylesheet">
<style>
  :root{
    --ink:#2b2b2b;
    --muted:#555;
    --red:#f3101f;
    --red-light:#ff2c49;
    --white:#ffffff;
    --footer-top:#2c2c2c;
    --footer-bottom:#0e0e0e;
    --footer-bar:#161616;
    --footer-text:#d8d8d8;
  }
  *{margin:0;padding:0;box-sizing:border-box}
  html,body{width:969px;height:1200px;overflow:hidden;background:var(--white)}
  body{position:relative;font-family:'Open Sans',sans-serif;color:var(--ink)}
  a{color:inherit;text-decoration:none}
  .abs{position:absolute}

  /* header */
  .site-header{left:0;top:0;width:969px;height:76px;background:var(--white);border-bottom:1px solid #e4e4e4}
  .brand{left:168px;top:20px;display:flex;align-items:center;gap:8px;font-family:'Raleway',sans-serif;font-weight:700;font-size:26px;color:#2a2a2a;letter-spacing:.5px}
  .brand-mark{width:14px;height:14px;background:var(--red)}
  .main-nav{left:412px;top:30px;display:flex;gap:24px;font-family:'Raleway',sans-serif;font-size:12.5px;color:#333}

  /* hero */
  .hero{left:0;top:76px;width:969px;height:353px;background:linear-gradient(100deg,#c9d2dc 0%,#e6ebf0 30%,#dcd6d0 55%,#b9a898 72%,#e8e6e4 90%,#f3f3f3 100%)}
  .hero-title{left:170px;top:212px;font-family:'Raleway',sans-serif;font-weight:700;color:#333}
  .hero-title .line1{display:block;font-size:24px;letter-spacing:.3px}
  .hero-title .line2{display:block;font-size:18.5px;margin-top:4px}
  .hero-dots{left:455px;top:378px;display:flex;gap:4px}
  .hero-dots span{width:13px;height:13px;border-radius:50%;background:#111}
  .hero-dots span.active{background:var(--red)}

  /* feature cards */
  .card-panel{left:160px;top:399px;width:646px;height:156px;background:var(--white);box-shadow:0 10px 24px rgba(0,0,0,.18)}
  .feature-card{top:410px;width:205px;height:134px;overflow:hidden}
  .feature-card .media{position:absolute;inset:0}
  .feature-card .caption{position:absolute;left:0;bottom:0;width:100%;height:34px;background:rgba(40,40,40,.82);display:flex;align-items:center;justify-content:space-between;padding:0 10px 0 19px;font-family:'Raleway',sans-serif;font-weight:600;font-size:12px;color:var(--white);letter-spacing:.2px}
  .card-why{left:171px}
  .card-why .media{background:linear-gradient(135deg,#c8d3dd,#8fa0b0 60%,#5d6b78)}
  .card-what{left:383px}
  .card-what .media{background:linear-gradient(135deg,#2b3a44,#4f6a72 50%,#1d2a30)}
  .card-whom{left:593px}
  .card-whom .media{background:linear-gradient(135deg,#4a4a4a,#8a8a8a 50%,#3a3a3a)}

  /* benefits band */
  .benefits{left:0;top:562px;width:969px;height:175px;background:linear-gradient(180deg,var(--red-light),var(--red))}
  .benefit{top:606px;width:150px;text-align:center;color:var(--white)}
  .benefit svg{display:block;margin:0 auto 8px}
  .benefit h3{font-family:'Raleway',sans-serif;font-weight:500;font-size:15px;margin-bottom:3px}
  .benefit p{font-size:8px;line-height:13.5px;color:#ffe3e6}
  .band-arrow{top:626px}

  /* overview */
  .about-title{left:173px;top:786px;font-family:'Raleway',sans-serif;font-weight:300;font-size:21px;color:#333}
  .about-lead{left:172px;top:820px;width:365px;font-size:8.8px;line-height:13.5px;color:var(--muted)}
  .about-body{left:172px;top:855px;width:370px;font-size:6.8px;line-height:13.6px;color:var(--muted)}
  .btn-more{left:172px;top:916px;width:75px;height:22px;background:var(--red);color:var(--white);font-size:8px;font-weight:600;display:flex;align-items:center;justify-content:center;letter-spacing:.2px}
  .video{left:563px;top:791px;width:236px;height:142px;background:linear-gradient(120deg,#e8eef2 0%,#5fb8cf 35%,#1c8fb0 70%,#0f6f90 100%)}
  .play{left:666px;top:848px}

  /* footer */
  .site-footer{left:0;top:984px;width:969px;height:171px;background:linear-gradient(180deg,var(--footer-top),var(--footer-bottom))}
  .footer-col{top:1017px;color:var(--footer-text)}
  .footer-col h4{font-family:'Raleway',sans-serif;font-weight:500;font-size:14px;color:var(--white);margin-bottom:5px}
  .footer-col li{list-style:none;font-size:8.5px;line-height:18.8px}
  .footer-bar{left:0;top:1155px;width:969px;height:45px;background:var(--footer-bar)}
  .copyright{left:179px;top:1173px;font-size:7px;color:#aaa}
  .social{left:730px;top:1171px;display:flex;gap:8px}
  .social span{width:12px;height:12px;border-radius:50%;background:#bdbdbd}
</style>
</head>
<body>

<header class="site-header abs"></header>
<div class="brand abs"><span>BrambleAI</span><span class="brand-mark"></span></div>
<nav class="main-nav abs">
  <a href="#overview">Overview</a><a href="#why">Why It</a><a href="#features">Features</a><a href="#engine">Engine</a><a href="#performance">Results</a><a href="#enquiry">Enquiry</a>
</nav>

<section id="overview" class="hero abs" role="img" aria-label="Photo of data scientists in lab coats studying a computer screen"></section>
<h1 class="hero-title abs"><span class="line1">APPLICATION DEVELOPMENT</span><span class="line2">AND VIRTUAL DATA ANALYSIS</span></h1>
<div class="hero-dots abs"><span class="active"></span><span></span><span></span><span></span></div>

<div class="card-panel abs"></div>
<a href="#why" id="why" class="feature-card card-why abs">
  <div class="media" role="img" aria-label="Photo of hands typing on a laptop"></div>
  <div class="caption"><span>WHY CHOOSE US</span><svg width="9" height="18" viewBox="0 0 9 18"><path d="M1 1l7 8-7 8" fill="none" stroke="#fff" stroke-width="1.2"/></svg></div>
</a>
<a href="#engine" class="feature-card card-what abs">
  <div class="media" role="img" aria-label="Photo of a phone showing analytics charts"></div>
  <div class="caption"><span>WHAT WE DO</span><svg width="9" height="18" viewBox="0 0 9 18"><path d="M1 1l7 8-7 8" fill="none" stroke="#fff" stroke-width="1.2"/></svg></div>
</a>
<a href="#enquiry" class="feature-card card-whom abs">
  <div class="media" role="img" aria-label="Photo of a hand holding metal gears"></div>
  <div class="caption"><span>FOR WHOM</span><svg width="9" height="18" viewBox="0 0 9 18"><path d="M1 1l7 8-7 8" fill="none" stroke="#fff" stroke-width="1.2"/></svg></div>
</a>

<section id="features" class="benefits abs"></section>
<svg class="band-arrow abs" style="left:136px" width="16" height="40" viewBox="0 0 16 40"><path d="M15 1L1 20l14 19" fill="none" stroke="#fff" stroke-width="1.2"/></svg>
<svg class="band-arrow abs" style="left:812px" width="16" height="40" viewBox="0 0 16 40"><path d="M1 1l14 19L1 39" fill="none" stroke="#fff" stroke-width="1.2"/></svg>

<div class="benefit abs" style="left:165px">
  <svg width="40" height="34" viewBox="0 0 40 34"><rect x="1.5" y="1.5" width="37" height="24" rx="2" fill="none" stroke="#fff" stroke-width="3"/><rect x="16" y="26" width="8" height="4" fill="#fff"/><rect x="10" y="30" width="20" height="3" fill="#fff"/></svg>
  <h3>Automated</h3>
  <p>Mauris vel lacus vitae felis vestibulum volutpat Etiam est nunc venen</p>
</div>
<div class="benefit abs" style="left:327px">
  <svg width="28" height="40" viewBox="0 0 28 40"><path d="M14 2a12 12 0 0 0-7 21.7c1.5 1.2 2 2.5 2 4.3v1h10v-1c0-1.8.5-3.1 2-4.3A12 12 0 0 0 14 2z" fill="none" stroke="#fff" stroke-width="2.6"/><rect x="9" y="31" width="10" height="3" fill="#fff"/><rect x="10.5" y="35.5" width="7" height="3" rx="1" fill="#fff"/></svg>
  <h3>Intelligent</h3>
  <p>Mauris vel lacus vitae felis vestibulum volutpat Etiam est nunc venen</p>
</div>
<div class="benefit abs" style="left:488px">
  <svg width="38" height="38" viewBox="0 0 38 38"><path d="M34 8l-6 6-4-4 6-6a9 9 0 0 0-11 11L4 30a3 3 0 0 0 4 4l15-15A9 9 0 0 0 34 8z" fill="#fff"/></svg>
  <h3>Easy to Adopt</h3>
  <p>Mauris vel lacus vitae felis vestibulum volutpat Etiam est nunc venen</p>
</div>
<div class="benefit abs" style="left:650px">
  <svg width="32" height="36" viewBox="0 0 32 36"><circle cx="16" cy="10" r="9" fill="#fff"/><path d="M1 35c0-9 6-14 15-14s15 5 15 14z" fill="#fff"/></svg>
  <h3 style="margin-top:9px">Self Learning</h3>
  <p>Mauris vel lacus vitae felis vestibulum volutpat Etiam est nunc venen</p>
</div>

<section id="engine">
<h2 class="about-title abs">About the Engine</h2>
<p class="about-lead abs">Curabitur iaculis tempus eros Curabitur vel mi sit amet magna malesuada ultrices Ut nisi erat fermentum vel congue id euismod in elit Fusce ultricies orci ac feugiat</p>
<p class="about-body abs">Morbi ornare gravida elit Integer congue augue et malesuada iaculis ipsum dui aliquet felis at cursus magna nisl nec elit Praesent elementum elit at tellus nec ultricies sit amet porttitor mattis enim In massa libero interdum nec interdum vel blandit sed nulla In ullamcorper est eget tempor cursus neque mi consectetuer mi a ultricies massa est sed nisl Class aptent taciti</p>
<a href="#performance" class="btn-more abs">READ MORE</a>
<div class="video abs" role="img" aria-label="Video still of a man using a tablet with floating data charts"></div>
<svg class="play abs" width="30" height="30" viewBox="0 0 30 30"><circle cx="15" cy="15" r="14" fill="#fff"/><path d="M12 9l9 6-9 6z" fill="#111"/></svg>
</section>

<footer id="enquiry" class="site-footer abs"></footer>
<div class="footer-col abs" style="left:183px"><h4>Product</h4><ul><li>Overview</li><li>How It Works</li><li>Architecture</li><li>Performance</li></ul></div>
<div class="footer-col abs" style="left:306px"><h4>Features</h4><ul><li>Automated</li><li>Intelligent</li><li>Easy to Adopt</li><li>Self Learning</li></ul></div>
<div class="footer-col abs" style="left:470px"><h4>Resources</h4><ul><li>Infosheet</li><li>Integration</li><li>FAQ</li><li>Enquiry</li></ul></div>
<div class="footer-col abs" style="left:604px"><h4>Enquiries</h4><ul><li>enquiry@brambleai.example</li></ul></div>
<div class="footer-bar abs"></div>
<p class="copyright abs">© 2015 BrambleAI &nbsp;All right reserved &nbsp;Term of Use</p>
<div class="social abs" aria-label="Social links"><span></span><span></span><span></span><span></span></div>

</body>
</html>
```